Business Card for a Jewellery Brand

Business card for an upscale jewellery brand. Attached is the brand logo and icon and color board. I am looking for two card versions: one for the founder and one is generic. The card should be elegant and convey upscale and premium feel. I am open to both square and rectangle card shapes.

Industry/Entity Type

Jewelry

Contact Information for Business Card

Two cards: (1) Sunela Parvaniya (Founder) (2) General
(1) Sunela Parvaniya card should have Name: Sunela Parvaniya, Title: Founder Email id: sunela@quiremo.com.au. Phone no: +61452913307
(2) Generic card should have Email id: info@quiremo.com.au. Phone no: +61436207518

Requirements
Must have
• Workmark
• ICON
• Phone no
• Email ID
• ABN: 58219740312 (Note: ABN is Business number in Australia)
• Website: www.quiremo.com.au
• Instagram: quiremo_jewellery
• Facebook: @quiremojewellery
Nice to have
• Tagline

```html
<!DOCTYPE html>
<html lang="en">
<head>
<meta charset="utf-8">
<title>Quiremo Jewellery – Business Cards</title>
<link rel="stylesheet" href="https://fonts.googleapis.com/css2?family=Open+Sans:wght@300;400;600;700&display=swap">
<style>
  :root {
    --page-bg: #e9e7e6;
    --card-white: #f7f6f6;
    --blush: #e1918d;
    --blush-soft: #f3e4e3;
    --pattern-tone: #efdcdb;
    --ink-light: #ffffff;
  }
  * { margin: 0; padding: 0; box-sizing: border-box; }
  html, body {
    width: 1200px;
    height: 900px;
    overflow: hidden;
    background: var(--page-bg);
    font-family: "Open Sans", Arial, sans-serif;
  }
  .stage {
    position: relative;
    width: 1200px;
    height: 900px;
  }
  .card {
    position: absolute;
    left: 250px;
    width: 700px;
    height: 400px;
    overflow: hidden;
    box-shadow: 0 10px 28px rgba(0,0,0,0.18);
  }
  .card--back { top: 40px; background: var(--card-white); }
  .card--front { top: 465px; background: var(--blush); }

  .pattern-fill {
    position: absolute;
    inset: 0;
    background: linear-gradient(135deg, var(--blush-soft), var(--pattern-tone) 50%, var(--blush-soft));
  }
  .card-shape { position: absolute; inset: 0; }

  .brand {
    position: absolute;
    display: flex;
    flex-direction: column;
    align-items: center;
    color: var(--blush);
  }
  .brand__dot {
    width: 64px;
    height: 64px;
    border: 3px solid var(--blush);
    border-radius: 50%;
    margin-bottom: 22px;
  }
  .brand__name {
    font-weight: 300;
    font-size: 46px;
    letter-spacing: 14px;
    margin-right: -14px;
    line-height: 1;
  }
  .card--back .brand { left: 0; right: 0; top: 95px; }
  .card--front .brand { left: 330px; right: 0; top: 60px; }

  .contact {
    position: absolute;
    left: 42px;
    top: 175px;
    color: var(--ink-light);
  }
  .contact__name { font-weight: 700; font-size: 17px; line-height: 1.2; }
  .contact__role { font-weight: 400; font-size: 15px; margin-bottom: 14px; }
  .contact__abn { font-weight: 300; font-size: 13px; margin-bottom: 8px; }
  .contact__list { list-style: none; }
  .contact__item {
    display: flex;
    align-items: center;
    gap: 10px;
    font-weight: 300;
    font-size: 13px;
    line-height: 21px;
  }
  .contact__icon { width: 13px; height: 13px; flex: none; }
  .contact__tagline {
    margin-top: 8px;
    font-weight: 600;
    font-size: 13px;
    letter-spacing: 0.5px;
  }
</style>
</head>
<body>
<main class="stage">

  <section class="card card--back" aria-label="Business card back">
    <div class="pattern-fill" role="img" aria-label="Faint repeating brand-icon pattern in pale blush"></div>
    <div class="brand">
      <span class="brand__dot"></span>
      <span class="brand__name">QUIREMO</span>
    </div>
  </section>

  <section class="card card--front" aria-label="Business card front">
    <svg class="card-shape" viewBox="0 0 700 400" aria-hidden="true">
      <polygon points="270,0 700,0 700,285 300,240 250,130" fill="var(--card-white)"/>
    </svg>

    <div class="brand">
      <span class="brand__dot"></span>
      <span class="brand__name">QUIREMO</span>
    </div>

    <div class="contact">
      <p class="contact__name">Sunela Parvaniya</p>
      <p class="contact__role">Founder</p>
      <p class="contact__abn">ABN: 58219740312</p>
      <ul class="contact__list">
        <li class="contact__item">
          <svg class="contact__icon" viewBox="0 0 14 14"><rect x="3.5" y="0.5" width="7" height="13" rx="1.2" fill="none" stroke="#fff" stroke-width="1.2"/><circle cx="7" cy="11.2" r="0.8" fill="#fff"/></svg>
          <span>+61452913307</span>
        </li>
        <li class="contact__item">
          <svg class="contact__icon" viewBox="0 0 14 14"><rect x="0.5" y="2.5" width="13" height="9" fill="#fff"/><polyline points="0.5,2.5 7,8 13.5,2.5" fill="none" stroke="var(--blush)" stroke-width="1.2"/></svg>
          <span>sunela@quiremo.com.au</span>
        </li>
        <li class="contact__item">
          <svg class="contact__icon" viewBox="0 0 14 14"><circle cx="7" cy="7" r="6" fill="none" stroke="#fff" stroke-width="1.2"/><ellipse cx="7" cy="7" rx="2.6" ry="6" fill="none" stroke="#fff" stroke-width="1"/><line x1="1" y1="7" x2="13" y2="7" stroke="#fff" stroke-width="1"/></svg>
          <span>www.quiremo.com.au</span>
        </li>
        <li class="contact__item">
          <svg class="contact__icon" viewBox="0 0 14 14"><rect x="1" y="1" width="12" height="12" rx="2" fill="#fff"/></svg>
          <span>quiremo_jewellery</span>
        </li>
        <li class="contact__item">
          <svg class="contact__icon" viewBox="0 0 14 14"><rect x="1" y="1" width="12" height="12" rx="3" fill="none" stroke="#fff" stroke-width="1.4"/></svg>
          <span>@quiremojewellery</span>
        </li>
      </ul>
      <p class="contact__tagline">LOVE IS IN THE AIR</p>
    </div>
  </section>

</main>
</body>
</html>
```